Marbrook Cupcakes Website

We need a new website. We make Texas-size gourmet cupcakes and cupcake jars. We want a website similar to the one KEYlane is hosting and made. They're charging too much per month. I would like to have Blu Otter host it. see the current site at: marbrookcupcakes.com

```html
<!DOCTYPE html>
<html lang="en">
<head>
<meta charset="utf-8">
<title>Marbrook Cupcakes</title>
<link href="https://fonts.googleapis.com/css2?family=Arimo:wght@400;700&family=Lato:wght@400;700&display=swap" rel="stylesheet">
<style>
:root{
  --teal:#6ec8d0;
  --teal-soft:#f3fafb;
  --brown:#4a2210;
  --brown-mid:#7a4a2a;
  --ink:#111;
  --muted:#777;
  --line:#cfd8da;
  --star:#f0a020;
  --white:#fff;
}
*{margin:0;padding:0;box-sizing:border-box}
html,body{width:1200px;height:3985px;overflow:hidden;background:var(--white)}
body{position:relative;font-family:"Lato",sans-serif;color:var(--ink)}
.abs{position:absolute}
.heading{font-family:"Arimo",sans-serif;font-weight:700}
.btn{position:absolute;display:flex;align-items:center;justify-content:center;border-radius:24px;font-family:"Arimo",sans-serif;font-weight:700;font-size:17px;box-shadow:0 3px 6px rgba(0,0,0,.25)}
.btn-dark{background:var(--brown);color:var(--white)}
.btn-light{background:var(--white);color:var(--ink)}

/* header */
.site-header{position:absolute;left:0;top:0;width:1200px;height:102px;background:var(--white);z-index:3}
.brand-badge{position:absolute;left:86px;top:0;width:206px;height:206px;border-radius:50%;background:var(--white);border:12px solid #c9b3a4;border-top:none;z-index:4;display:flex;flex-direction:column;align-items:center;justify-content:center;gap:8px}
.brand-dot{width:70px;height:70px;border-radius:50%;background:var(--teal)}
.brand-name{font-family:"Lato",sans-serif;font-weight:700;font-size:16px;color:var(--brown)}
.nav a{position:absolute;top:44px;font-size:15px;color:var(--ink);text-decoration:none;font-family:"Arimo",sans-serif}
.nav a.active{color:var(--teal);border-bottom:1px solid var(--teal);padding-bottom:2px}
.call-box{position:absolute;left:959px;top:0;width:241px;height:102px;background:var(--teal);clip-path:polygon(60px 0,100% 0,100% 100%,0 100%)}
.call-box .label{position:absolute;left:111px;top:24px;color:var(--white);font-family:"Arimo",sans-serif;font-size:15px}
.call-box .num{position:absolute;left:38px;top:56px;color:var(--white);font-family:"Arimo",sans-serif;font-size:26px}

/* hero */
.hero{position:absolute;left:0;top:102px;width:1200px;height:625px}
.hero-photo{position:absolute;inset:0;background:linear-gradient(90deg,#5c3120 0%,#7b4429 45%,#b8835a 70%,#e9d9b8 85%,#8b5a36 100%)}
.hero-title{position:absolute;left:110px;color:var(--white);font-family:"Arimo",sans-serif}
.hero-text{position:absolute;left:110px;top:302px;width:360px;color:var(--white);font-size:15px;line-height:29px}

/* about */
.section-title{position:absolute;left:0;width:1200px;text-align:center;font-size:43px}
.section-title span{color:var(--brown)}
.about-mark{position:absolute;left:162px;top:923px;width:410px;height:500px;display:flex;flex-direction:column;align-items:center;justify-content:center;gap:30px}
.about-mark .circle{width:300px;height:300px;border-radius:50%;background:var(--teal)}
.about-mark .name{font-family:"Lato",sans-serif;font-weight:700;font-size:38px;color:var(--brown)}
.about-text{position:absolute;left:640px;top:945px;width:421px;font-size:15px;line-height:29.2px;color:#333;text-align:justify}

/* flavours */
.flavours{position:absolute;left:0;top:1550px;width:1200px;height:1131px;background:var(--teal-soft)}
.flavour{position:absolute;width:430px;height:180px}
.flavour .photo{position:absolute;left:0;top:0;width:170px;height:178px;border-radius:3px}
.flavour .stars{position:absolute;left:192px;top:2px;color:var(--star);font-size:15px;letter-spacing:1px}
.flavour h3{position:absolute;left:192px;top:32px;font-family:"Lato",sans-serif;font-weight:700;font-size:20px;color:#222}
.flavour .sub{position:absolute;left:192px;top:68px;font-size:15px;color:var(--muted)}
.flavour .desc{position:absolute;left:192px;top:100px;width:240px;font-size:12px;line-height:26px;color:#999}
.flavour .more{position:absolute;left:192px;top:158px;width:240px;display:flex;align-items:center;gap:8px;color:var(--teal);font-size:18px}
.flavour .more i{flex:0 0 130px;border-bottom:2px dotted var(--teal);height:0;margin-top:8px}
.rule-v{position:absolute;left:599px;top:1720px;width:1px;height:752px;background:var(--line)}
.rule-h{position:absolute;left:111px;width:978px;height:1px;background:var(--line)}

/* specials */
.specials{position:absolute;left:0;top:2681px;width:1200px;height:882px;background:var(--teal)}
.specials p{font-size:15px;line-height:29px}
.arrow{position:absolute;width:18px;height:12px}

/* footer */
.footer-brand{position:absolute;left:155px;top:3640px;width:170px;height:200px;display:flex;flex-direction:column;align-items:center;justify-content:center;gap:12px}
.footer-brand .circle{width:110px;height:110px;border-radius:50%;background:var(--teal)}
.footer-brand .name{font-weight:700;font-size:16px;color:var(--brown)}
.social{position:absolute;left:112px;top:3795px;width:30px;height:30px;border-radius:50%;border:2px solid var(--teal)}
.foot-col h4{position:absolute;font-family:"Arimo",sans-serif;font-weight:400;font-size:21px;color:#222}
.foot-col a{position:absolute;font-size:15px;color:#333;text-decoration:none}
.contact-item{position:absolute;left:848px;display:flex;gap:14px;font-size:15px;line-height:27px;color:#222;align-items:flex-start}
.contact-item .ico{flex:0 0 30px;height:30px;border-radius:50%;background:var(--teal);display:flex;align-items:center;justify-content:center}
.footer-rule{position:absolute;left:111px;top:3886px;width:978px;height:1px;background:var(--line)}
.copyright{position:absolute;left:0;top:3922px;width:1200px;text-align:center;font-size:15px;color:#111}
</style>
</head>
<body>

<header class="site-header">
  <nav class="nav">
    <a href="#" class="active" style="left:416px">Home</a>
    <a href="#" style="left:501px">Menu</a>
    <a href="#" style="left:582px">Cupcake</a>
    <a href="#" style="left:690px">Shop</a>
    <a href="#" style="left:769px">Blog</a>
    <a href="#" style="left:843px">Contact Us</a>
  </nav>
  <div class="call-box">
    <svg class="abs" style="left:76px;top:20px" width="26" height="26" viewBox="0 0 26 26"><circle cx="13" cy="13" r="12" fill="#fff"/><path d="M9 7c1 0 2 3 1.5 4s-1 1 0 2.5 2 2.5 3 2.7 1.5-1 2.5-.8 3 1.5 2.7 2.5-1.5 2-3 1.8S10 18 8 14 7.5 7 9 7z" fill="#6ec8d0"/></svg>
    <div class="label">Call Us Today</div>
    <div class="num">+1 555 014 2290</div>
  </div>
</header>
<div class="brand-badge"><div class="brand-dot"></div><div class="brand-name">Marbrook Cupcakes</div></div>

<section class="hero">
  <div class="hero-photo" role="img" aria-label="Photo of a lemon-topped cupcake with white frosting on a wooden table"></div>
  <h1 class="hero-title" style="top:170px;font-size:46px;font-weight:400">Welcome to</h1>
  <h1 class="hero-title" style="top:228px;font-size:52px;font-weight:400;left:107px">Marbrook Cupcakes</h1>
  <p class="hero-text">Lorem ipsum dolor sit amet, consectetur adipiscing elit, sed do eiusmod tempor incididunt ut labore et dolore magna aliqua.</p>
  <div class="btn btn-light" style="left:111px;top:413px;width:118px;height:40px;font-size:16px">Shop Now</div>
  <svg class="abs" style="left:0;top:545px" width="1200" height="80" viewBox="0 0 1200 80" preserveAspectRatio="none">
    <path d="M0 40 L60 30 L120 42 L200 28 L300 38 L420 24 L520 34 L640 20 L760 30 L880 18 L980 26 L1080 14 L1200 10 L1200 80 L0 80 Z" fill="#fff"/>
  </svg>
</section>

<h2 class="section-title heading" style="top:826px">About Marbrook <span>Cupcake</span></h2>
<div class="about-mark"><div class="circle"></div><div class="name">Marbrook Cupcakes</div></div>
<p class="about-text">Sed ut perspiciatis unde omnis iste natus error sit voluptatem accusantium doloremque laudantium, totam rem aperiam, eaque ipsa quae ab illo inventore veritatis et quasi architecto beatae vitae dicta sunt explicabo. Nemo enim ipsam voluptatem quia voluptas sit aspernatur aut odit aut fugit, sed quia consequuntur magni dolores eos qui ratione voluptatem sequi nesciunt. Neque porro quisquam est, qui dolorem ipsum quia dolor sit amet, consectetur, adipisci velit, sed quia non numquam eius modi tempora incidunt ut labore et dolore magnam aliquam quaerat voluptatem. Ut enim ad minima veniam, quis nostrum exercitationem ullam corporis suscipit laboriosam, nisi ut aliquid ex ea commodi consequatur? Quis autem vel eum iure reprehenderit qui in ea voluptate velit esse quam nihil molestiae consequatur, vel illum qui dolorem eum fugiat quo voluptas nulla pariatur.</p>
<div class="btn btn-dark" style="left:640px;top:1401px;width:139px;height:47px">Read More</div>

<section class="flavours"></section>
<h2 class="section-title heading" style="top:1624px">Our <span>Flavours</span></h2>
<div class="rule-v"></div>
<div class="rule-h" style="top:1960px"></div>
<div class="rule-h" style="top:2215px"></div>

<article class="flavour" style="left:111px;top:1737px">
  <div class="photo" role="img" aria-label="Photo of a cookie and cream cupcake" style="background:linear-gradient(160deg,#8a5233,#3a2a24 60%,#c9b9a8)"></div>
  <div class="stars">★★★★★</div><h3>Cookie &amp; Cream</h3><div class="sub">Duis aute irure dolor</div>
  <div class="desc">Lorem ipsum dolor sit amet, consectetur adipiscing elit</div>
  <div class="more"><i></i>View More</div>
</article>
<article class="flavour" style="left:665px;top:1737px">
  <div class="photo" role="img" aria-label="Photo of a chocolate cream cupcake" style="background:linear-gradient(160deg,#8a4a2a,#e6ddd3 50%,#6a4030)"></div>
  <div class="stars">★★★★★</div><h3>Chocolate cream</h3><div class="sub">Excepteur sint occaecat</div>
  <div class="desc">Duis aute irure dolor in reprehenderit in voluptate velit esse cillum</div>
  <div class="more"><i></i>View More</div>
</article>
<article class="flavour" style="left:111px;top:1999px">
  <div class="photo" role="img" aria-label="Photo of a red velvet cupcake" style="background:linear-gradient(160deg,#9a5a3a,#efe6e0 50%,#b02030)"></div>
  <div class="stars">★★★★★</div><h3>Red Velvet</h3><div class="sub">Deserunt mollit anim</div>
  <div class="desc">Duis aute irure dolor in reprehenderit in voluptate velit esse cillum</div>
  <div class="more"><i></i>View More</div>
</article>
<article class="flavour" style="left:665px;top:1999px">
  <div class="photo" role="img" aria-label="Photo of a caramel peanut cupcake" style="background:linear-gradient(160deg,#8a4a2a,#c8955c 50%,#e0d2c4)"></div>
  <div class="stars">★★★★★</div><h3>Caramel Crunch</h3><div class="sub">Quis nostrud exercitation</div>
  <div class="desc">Excepteur sint occaecat cupidatat non proident, sunt in culpa qui</div>
  <div class="more"><i></i>View More</div>
</article>
<article class="flavour" style="left:111px;top:2255px">
  <div class="photo" role="img" aria-label="Photo of a chocolate mousse cupcake" style="background:linear-gradient(160deg,#7a4a30,#8a4a28 45%,#3a2820)"></div>
  <div class="stars">★★★★★</div><h3>Chocolate Mousse</h3><div class="sub">Occaecat cupidatat non</div>
  <div class="desc">Excepteur sint occaecat cupidatat non proident, sunt in culpa qui</div>
  <div class="more"><i></i>View More</div>
</article>
<article class="flavour" style="left:665px;top:2255px">
  <div class="photo" role="img" aria-label="Photo of a German chocolate cupcake" style="background:linear-gradient(160deg,#8a4a2a,#b98a55 45%,#5a3024)"></div>
  <div class="stars">★★★★★</div><h3>German Chocolate</h3><div class="sub">Dolor in reprehenderit</div>
  <div class="desc">Duis aute irure dolor in reprehenderit in voluptate velit esse cillum</div>
  <div class="more"><i></i>View More</div>
</article>
<div class="btn btn-dark" style="left:534px;top:2551px;width:134px;height:47px">View More</div>

<section class="specials">
  <h2 class="abs heading" style="left:111px;top:96px;font-size:43px">Daily Specials</h2>
  <p class="abs" style="left:111px;top:150px;width:500px">Lorem ipsum dolor sit amet, consectetur adipiscing elit, sed do eiusmod tempor incididunt ut labore et dolore magna aliqua. Ut enim ad minim veniam, quis nostrud exercitation ullamco laboris nisi ut aliquip ex ea commodo consequat.</p>
  <div class="abs" role="img" aria-label="Photo of a strawberry-topped cupcake" style="left:111px;top:305px;width:447px;height:450px;background:linear-gradient(170deg,#7a3c20,#f0d9d0 45%,#c8662e 80%,#6a3018)"></div>
  <div class="abs" style="left:108px;top:775px;font-family:'Arimo',sans-serif;font-size:25px">Stawberry</div>
  <svg class="arrow" style="left:537px;top:789px" viewBox="0 0 18 12"><path d="M1 6h15M11 1l5 5-5 5" stroke="#111" stroke-width="2" fill="none"/></svg>
  <div class="abs" role="img" aria-label="Photo of a wedding cake cupcake with white frosting" style="left:640px;top:97px;width:449px;height:449px;background:linear-gradient(170deg,#a05a30,#f5efdc 40%,#efe6cf 70%,#8a4a2a)"></div>
  <div class="abs" style="left:638px;top:568px;font-family:'Arimo',sans-serif;font-size:29px">Wedding Cake</div>
  <svg class="arrow" style="left:1071px;top:574px" viewBox="0 0 18 12"><path d="M1 6h15M11 1l5 5-5 5" stroke="#111" stroke-width="2" fill="none"/></svg>
  <p class="abs" style="left:640px;top:611px;width:449px;text-align:justify">Lorem ipsum dolor sit amet, consectetur adipiscing elit, sed do eiusmod tempor incididunt ut labore et dolore magna aliqua. Ut enim ad minim veniam, quis nostrud exercitation ullamco laboris nisi ut aliquip ex ea commodo consequat.</p>
  <div class="btn btn-light" style="left:640px;top:753px;width:118px;height:42px">Buy Now</div>
</section>

<footer>
  <div class="footer-brand"><div class="circle"></div><div class="name">Marbrook Cupcakes</div></div>
  <div class="social"></div>
  <div class="foot-col">
    <h4 style="left:422px;top:3636px">Quick Links</h4>
    <a style="left:426px;top:3682px">Home</a><a style="left:426px;top:3716px">About</a><a style="left:426px;top:3751px">Flavours</a><a style="left:426px;top:3786px">Blog</a><a style="left:426px;top:3820px">Contact us</a>
  </div>
  <div class="foot-col">
    <h4 style="left:642px;top:3636px">Help Links</h4>
    <a style="left:643px;top:3682px">FAQ</a><a style="left:643px;top:3716px">Terms of use</a><a style="left:643px;top:3751px">Privacy Policy</a><a style="left:643px;top:3786px">Support Links</a><a style="left:643px;top:3820px">Conditions</a>
  </div>
  <div class="foot-col"><h4 style="left:847px;top:3636px">Contact Us</h4></div>
  <div class="contact-item" style="top:3676px"><span class="ico"><svg width="14" height="18" viewBox="0 0 14 18"><path d="M7 17s6-6 6-10A6 6 0 0 0 1 7c0 4 6 10 6 10z" fill="#fff"/><circle cx="7" cy="7" r="2.2" fill="#6ec8d0"/></svg></span><span>Marbrook Cupcake<br>United States</span></div>
  <div class="contact-item" style="top:3746px"><span class="ico"><svg width="16" height="16" viewBox="0 0 26 26"><path d="M6 3c2 0 4 5 3 6.5s-2 1.5 0 4.5 4 4.5 5.5 4.5 2-2 3.5-1.5 6 2.5 5.5 4-3 3.5-5.5 3S8 20 5 14 3 3 6 3z" fill="#fff"/></svg></span><span>+1 555 014 2290</span></div>
  <div class="contact-item" style="top:3797px"><span class="ico"><svg width="16" height="12" viewBox="0 0 16 12"><rect x="0.5" y="0.5" width="15" height="11" rx="1" fill="#fff"/><path d="M1 1l7 6 7-6" stroke="#6ec8d0" stroke-width="1.5" fill="none"/></svg></span><span>hello@marbrookcupcakes.com</span></div>
  <div class="footer-rule"></div>
  <div class="copyright">Copyrights@2025.Marbrook Cupcake.All Rights Reserved</div>
</footer>

</body>
</html>
```